Journal Cover Design Project

The Worldwide Review of Rising Trade Systems is a professional journal which aims to provide an international platform for publication of original research on the emerging economies.
The journal is published three times a year and available by subscription. Currently, the cover design is the same for each issue. We are looking to redesign the cover (and interior) of our journal and would like a design that would allow us to change the color scheme for each issue or volume while maintaining a consistent design scheme.
Our design preference is simple and modern with good use of color. Many of our past publications have used abstract maps/globes but we are open to new ideas. We would need a creative way to include text on the cover, possibly a way to present the article titles or main topics for each issue. For example, we like the use of color and the general design in this image: http://www.pictavo.example/photos/moonlitpaperkite/5120448391/lightbox/
Below is a link to our most recent issue of the journal. You can see an example of the article titles, structure, etc. The website also shows the current cover of the journal (but we do not want the new design to be based off of the current one):
http://wrt.plovarhouse.example/content/4/2.toc

```html
<!DOCTYPE html>
<html lang="en">
<head>
<meta charset="utf-8">
<title>In the news — New Directions for Water Management in Indian Agriculture</title>
<link href="https://fonts.googleapis.com/css2?family=Arimo:wght@400;700&display=swap" rel="stylesheet">
<style>
  :root {
    --backdrop: #ffffff;
    --page: #ffffff;
    --page-edge: #e2e2e2;
    --band-green: #3cb54a;
    --pattern-dark: #0f7a3a;
    --pattern-light: #2fa24f;
    --body-tint: #d2e9cf;
    --body-text: #1f2a1f;
    --footer-green: #1f7a3c;
  }
  * { margin: 0; padding: 0; box-sizing: border-box; }
  html, body {
    width: 1200px; height: 849px; overflow: hidden;
    background: var(--backdrop);
    font-family: "Arimo", Arial, sans-serif;
  }
  .page {
    position: absolute; left: 338px; top: 75px;
    width: 522px; height: 683px;
    background: var(--page);
    border: 1px solid var(--page-edge);
  }
  .header-pattern {
    position: absolute; left: 26px; top: 29px;
    width: 467px; height: 56px;
    background: linear-gradient(180deg, var(--pattern-dark) 0%, var(--pattern-light) 100%);
  }
  .title-band {
    position: absolute; left: 26px; top: 85px;
    width: 467px; height: 75px;
    background: var(--band-green);
    color: #fff;
    padding: 14px 0 0 15px;
  }
  .section-label { font-weight: 700; font-size: 15px; line-height: 18px; }
  .article-title { font-weight: 400; font-size: 15.5px; line-height: 18px; }
  .article-body {
    position: absolute; left: 26px; top: 160px;
    width: 467px; height: 460px;
    background: var(--body-tint);
    display: flex; gap: 17px;
    padding: 14px 15px 0 15px;
  }
  .column { width: 210px; }
  .column p {
    font-size: 9.2px; line-height: 11.6px;
    color: var(--body-text);
    margin-bottom: 11.6px;
  }
  .footer {
    position: absolute; left: 26px; top: 627px;
    width: 467px; color: var(--footer-green);
  }
  .journal-name { font-weight: 700; font-size: 8.4px; letter-spacing: 0.1px; }
  .issue-line { font-size: 8.4px; margin-top: 1px; }
  .page-number {
    position: absolute; right: 0; top: -2px;
    font-size: 21px; font-weight: 400;
  }
</style>
</head>
<body>
  <div class="page">
    <div class="header-pattern" role="img" aria-label="Decorative green tiled grid pattern"></div>
    <div class="title-band">
      <div class="section-label">In the news</div>
      <div class="article-title">New Directions for Water Management<br>in Indian Agriculture</div>
    </div>
    <div class="article-body">
      <div class="column">
        <p>Despite several decades of large and expensive government programs to expand traditional surface irrigation systems, groundwater irrigated area has continued to grow inexorably—even in command areas of canals and tanks. Groundwater now irrigates more than double the area irrigated by surface water.</p>
        <p>The alarming drop in groundwater tables in parts of Northwestern and of Peninsular India, and the apparent high public cost of subsidizing the electricity for ground water pumping, has led to calls for limiting groundwater abstraction and further developing surface water systems. This reaction to the ground water challenge misses the point.</p>
        <p>The debate should not be about whether surface water schemes are preferable to groundwater use, or more generally how to build new infrastructure to increase water supply. Instead, the question is how to deliver a reliable service to improve agricultural productivity. Further surface water development (reservoirs, canals) will not reduce demand for ground water unless it can meet the requirement for “just-in-time” water without discriminating against tail-enders and/or small farmers.</p>
      </div>
      <div class="column">
        <p>Despite several decades of large and expensive government programs to expand traditional surface irrigation systems, groundwater irrigated area has continued to grow inexorably—even in command areas of canals and tanks. Groundwater now irrigates more than double the area irrigated by surface water. The alarming drop in groundwater tables in parts of Northwestern and of Peninsular India, and the apparent high public cost of subsidizing the electricity for ground water pumping, has led to calls for limiting groundwater abstraction and further developing surface water systems. This reaction to the ground water challenge misses the point.</p>
        <p>The debate should not be about whether surface water schemes are preferable to groundwater use, or more generally how to build new infrastructure to increase water supply. Instead, the question is how to deliver a reliable service to improve agricultural productivity. Further surface water development (reservoirs, canals) will not reduce demand for ground water unless it can meet the requirement for “just-in-time” water without discriminating against tail-enders and/or small farmers.</p>
      </div>
    </div>
    <div class="footer">
      <div class="journal-name">WORLDWIDE REVIEW OF RISING TRADE SYSTEMS</div>
      <div class="issue-line">Vol 4 Issue 2 • May 2012</div>
      <div class="page-number">01</div>
    </div>
  </div>
</body>
</html>
```